Design NEW business card

We would like a business card using the colour deep red wine or dark navy blue textured background (patterned or not, open to suggestions) with a high gloss debossed rose gold/copper RM Roland Mercer Jewellery business name (Provided). I have included images for your review we would like to keep our currently logo and business name on the front but you can change the layout and positioning. For the back of the card we are open to all suggestions/variations.
Business
Use our current RM Roland Mercer Jewellery logo (Provided image)

```html
<!DOCTYPE html>
<html lang="en">
<head>
<meta charset="utf-8">
<title>Roland Mercer Jewellery – Business Card</title>
<link rel="stylesheet" href="https://fonts.googleapis.com/css2?family=Montserrat:wght@400&family=Oswald:wght@500&family=Roboto:wght@400;500&display=swap">
<style>
  :root {
    --page-bg: #2a2a2b;
    --card-bg: #3b0f1d;
    --card-bg-deep: #2c0914;
    --card-line: rgba(255,255,255,.025);
    --card-edge: #4a1626;
    --copper: #c9946e;
    --text-light: #f4ecec;
    --text-muted: #d8c8cb;
    --divider: #c9b8bb;
  }
  * { box-sizing: border-box; margin: 0; padding: 0; }
  html, body {
    width: 1200px; height: 900px; overflow: hidden;
    background: var(--page-bg);
  }
  .canvas {
    position: relative; width: 1200px; height: 900px;
    display: flex; flex-direction: column; align-items: center; justify-content: center; gap: 44px;
  }
  .card {
    position: relative; width: 680px; height: 388px;
    background:
      repeating-linear-gradient(45deg, var(--card-line) 0 1px, transparent 1px 4px),
      radial-gradient(ellipse at 40% 35%, var(--card-bg) 0%, var(--card-bg-deep) 100%);
    border: 1px solid var(--card-edge);
    box-shadow: 0 14px 30px rgba(0,0,0,.45);
  }
  /* Front */
  .card--front { display: flex; align-items: center; justify-content: center; }
  .brand { display: flex; align-items: center; gap: 20px; }
  .brand__dot { width: 14px; height: 14px; border-radius: 50%; background: var(--copper); flex: none; }
  .brand__text { display: flex; flex-direction: column; align-items: flex-end; }
  .brand__name {
    font-family: "Montserrat", sans-serif; font-weight: 400;
    font-size: 28px; letter-spacing: 7px; color: var(--copper);
    text-transform: uppercase; line-height: 1.3; white-space: nowrap;
  }
  .brand__sub {
    font-family: "Montserrat", sans-serif; font-weight: 400;
    font-size: 13px; letter-spacing: 17px; color: var(--copper);
    text-transform: uppercase; margin-top: 6px; margin-right: -17px; white-space: nowrap;
  }
  /* Back */
  .holder {
    position: absolute; left: 60px; top: 132px; width: 272px; text-align: right;
  }
  .holder__name {
    font-family: "Oswald", sans-serif; font-weight: 500; font-size: 40px;
    color: var(--copper); letter-spacing: .5px; line-height: 1.05; white-space: nowrap;
  }
  .holder__title {
    font-family: "Roboto", sans-serif; font-size: 17px; color: var(--text-muted);
    margin-top: 4px; letter-spacing: .3px;
  }
  .divider {
    position: absolute; left: 352px; top: 110px; width: 2px; height: 120px;
    background: linear-gradient(to bottom, transparent, var(--divider) 20%, var(--divider) 80%, transparent);
  }
  .contacts { position: absolute; left: 380px; top: 114px; list-style: none; }
  .contacts li {
    display: flex; align-items: center; gap: 12px; height: 23px;
    font-family: "Roboto", sans-serif; font-weight: 500; font-size: 17px; color: var(--text-light);
    white-space: nowrap;
  }
  .icon { width: 15px; height: 15px; flex: none; fill: var(--copper); }
  .address {
    position: absolute; left: 0; right: 0; bottom: 58px;
    display: flex; align-items: center; justify-content: center; gap: 8px;
    font-family: "Roboto", sans-serif; font-weight: 500; font-size: 18px; color: var(--text-light);
  }
  .address .icon { width: 16px; height: 18px; }
</style>
</head>
<body>
<main class="canvas">
  <section class="card card--front" aria-label="Card front">
    <div class="brand">
      <span class="brand__dot"></span>
      <div class="brand__text">
        <h1 class="brand__name">Roland Mercer</h1>
        <p class="brand__sub">Jewellery</p>
      </div>
    </div>
  </section>

  <section class="card card--back" aria-label="Card back">
    <div class="holder">
      <h2 class="holder__name">ADAM CLARKE</h2>
      <p class="holder__title">CEO/FOUNDER</p>
    </div>
    <div class="divider"></div>
    <ul class="contacts">
      <li>
        <svg class="icon" viewBox="0 0 16 16" aria-hidden="true"><path d="M3.5 1l2.4 3.2-1.5 1.6c.9 2 2.6 3.7 4.6 4.6l1.6-1.5L14 11.3 12.6 14C6.8 13.6 2.4 9.2 2 3.4z"/></svg>
        555 214 7630
      </li>
      <li>
        <svg class="icon" viewBox="0 0 16 16" aria-hidden="true"><path d="M4 1h8a1 1 0 0 1 1 1v12a1 1 0 0 1-1 1H4a1 1 0 0 1-1-1V2a1 1 0 0 1 1-1zm1 2v9h6V3zm3 10a.8.8 0 1 0 0 .01z"/></svg>
        555 398 4172
      </li>
      <li>
        <svg class="icon" viewBox="0 0 16 16" aria-hidden="true"><path d="M4 1h7l1 1v3H4zM1 6h14v7h-3v2H4v-2H1zm4 5v3h6v-3z"/></svg>
        555 602 8815
      </li>
      <li>
        <svg class="icon" viewBox="0 0 16 16" aria-hidden="true"><path d="M1 3h14v10H1zm1.5 1.2L8 8.5l5.5-4.3z"/></svg>
        hello@rmjewellery.com
      </li>
      <li>
        <svg class="icon" viewBox="0 0 16 16" aria-hidden="true"><circle cx="8" cy="8" r="7"/><path d="M1 8h14M8 1c-3 3.5-3 10.5 0 14M8 1c3 3.5 3 10.5 0 14" stroke="#3b0f1d" stroke-width="1.2" fill="none"/></svg>
        www.rmjewellery.com
      </li>
    </ul>
    <p class="address">
      <svg class="icon" viewBox="0 0 16 18" aria-hidden="true"><path d="M8 0a6 6 0 0 1 6 6c0 4.5-6 12-6 12S2 10.5 2 6a6 6 0 0 1 6-6zm0 3.5a2.5 2.5 0 1 0 0 5 2.5 2.5 0 0 0 0-5z"/></svg>
      1420 Willow Crest Road, Juneau, Alaska 99801
    </p>
  </section>
</main>
</body>
</html>
```